Animal Eye Clinic needs a Business card

We are a new veterinary ophthalmology practice (Ridgeline Pet Vision Care) and we need a business card designed. We only see animal eyes - we are not a regular veterinary clinic. We already have a logo. We are looking for a professional, good looking business card to hand out to our clients. We are looking for something simple but professional and contemporary. Our logo is likely the only picture/graphic that needs to be on the card.
Updates

Contact Information for Business Card

Delia Vossman, BSc, DVM, MSc, DipACVO
Veterinary Ophthalmologist

Phone: 250.418.3927
Email: ridgelinepetvisioncare@mailbox-example.net
Website: ridgelinepetvisioncare-example.net
Address: 1874 Thornbury Rd
Kelowna, BC, V1X 4M9

Colors

Designer to choose colors to be used in the design.

Requirements
Must have
• Our logo (attached)

```html
<!DOCTYPE html>
<html lang="en">
<head>
<meta charset="utf-8">
<title>Ridgeline Pet Vision Care – Business Card</title>
<link rel="stylesheet" href="https://fonts.googleapis.com/css2?family=Open+Sans:wght@400;600&family=Source+Sans+3:wght@600;700&display=swap">
<style>
  :root {
    --backdrop: #e7e5e2;
    --card: #f4f4f2;
    --teal: #1f6f7a;
    --teal-dark: #15555e;
    --ink: #4a4a4a;
    --ink-soft: #5c5c5c;
    --shadow: rgba(0,0,0,0.18);
  }
  * { box-sizing: border-box; margin: 0; padding: 0; }
  html, body {
    width: 1200px; height: 969px; overflow: hidden;
    background: var(--backdrop);
  }
  .canvas { position: relative; width: 1200px; height: 969px; }

  .card {
    position: absolute; left: 120px; top: 212px;
    width: 960px; height: 545px;
    background: var(--card);
    border-radius: 4px 300px 300px 4px / 4px 272px 272px 4px;
    box-shadow: 0 14px 40px var(--shadow);
    overflow: hidden;
  }

  .card__art {
    position: absolute; left: 520px; top: 0;
    width: 440px; height: 545px;
    background: linear-gradient(160deg, var(--teal) 0%, var(--teal-dark) 70%, #2d3b3e 100%);
  }

  .brand {
    position: absolute; left: 38px; top: 62px;
    display: flex; align-items: center; gap: 18px;
  }
  .brand__dot {
    width: 64px; height: 64px; border-radius: 50%;
    background: var(--teal); flex: none;
  }
  .brand__name {
    font-family: "Source Sans 3", sans-serif;
    font-weight: 700; font-size: 29px; line-height: 1.05;
    color: var(--teal); text-transform: uppercase; letter-spacing: 0.5px;
  }

  .person { position: absolute; left: 38px; top: 228px; }
  .person__name {
    font-family: "Source Sans 3", sans-serif; font-weight: 700;
    font-size: 24px; color: var(--teal); letter-spacing: 0.4px;
  }
  .person__creds { font-weight: 600; font-size: 17px; letter-spacing: 0; }
  .person__title {
    font-family: "Open Sans", sans-serif; font-size: 18px;
    color: var(--ink-soft); margin-top: 4px;
  }

  .contact {
    position: absolute; left: 38px; top: 352px;
    list-style: none;
    font-family: "Open Sans", sans-serif; font-size: 18px; color: var(--ink);
  }
  .contact__item { display: flex; align-items: flex-start; gap: 12px; line-height: 28px; }
  .contact__item--address { margin-bottom: 12px; }
  .contact__icon { width: 16px; height: 16px; margin-top: 6px; flex: none; fill: var(--teal); }
</style>
</head>
<body>
<div class="canvas">
  <div class="card">
    <div class="card__art" role="img" aria-label="Illustration of a horse, dog and cat in teal silhouettes"></div>

    <div class="brand">
      <span class="brand__dot"></span>
      <span class="brand__name">Ridgeline Pet<br>Vision Care</span>
    </div>

    <div class="person">
      <p class="person__name">DELIA VOSSMAN, <span class="person__creds">BSc, DVM, MSc, DipACVO</span></p>
      <p class="person__title">Veterinary Ophthalmologist</p>
    </div>

    <ul class="contact">
      <li class="contact__item contact__item--address">
        <svg class="contact__icon" viewBox="0 0 16 16"><path d="M8 0a5.5 5.5 0 0 0-5.5 5.5C2.5 9.6 8 16 8 16s5.5-6.4 5.5-10.5A5.5 5.5 0 0 0 8 0zm0 7.8a2.3 2.3 0 1 1 0-4.6 2.3 2.3 0 0 1 0 4.6z"/></svg>
        <span>1874 Thornbury Rd<br>Kelowna, BC, V1X 4M9</span>
      </li>
      <li class="contact__item">
        <svg class="contact__icon" viewBox="0 0 16 16"><path d="M3.6 0.8l2.2 2.9c.3.4.3 1-.1 1.4L4.5 6.3c.9 2.1 2.6 3.8 4.7 4.7l1.2-1.2c.4-.4 1-.4 1.4-.1l2.9 2.2c.4.3.5.9.1 1.3l-1.4 1.6c-.6.6-1.5.8-2.3.5C6.4 13.8 2.2 9.6.7 4.9.4 4.1.6 3.2 1.2 2.6L2.3.7c.4-.4 1-.3 1.3.1z"/></svg>
        <span>250.418.3927</span>
      </li>
      <li class="contact__item">
        <svg class="contact__icon" viewBox="0 0 16 16"><path d="M0 3h16v1.2L8 9 0 4.2z"/><path d="M0 5.8l8 4.8 8-4.8V13H0z"/></svg>
        <span>ridgelinepetvisioncare@mailbox-example.net</span>
      </li>
      <li class="contact__item">
        <svg class="contact__icon" viewBox="0 0 16 16"><path d="M8 0a8 8 0 1 0 0 16A8 8 0 0 0 8 0zm0 1.5c.9 0 1.9 1.8 2.2 4.5H5.8C6.1 3.3 7.1 1.5 8 1.5zM1.6 9.5a6.6 6.6 0 0 1 0-3h2.7a16 16 0 0 0 0 3zm4.2 0a14 14 0 0 1 0-3h4.4a14 14 0 0 1 0 3zM8 14.5c-.9 0-1.9-1.8-2.2-4.5h4.4c-.3 2.7-1.3 4.5-2.2 4.5zm3.7-5a16 16 0 0 0 0-3h2.7a6.6 6.6 0 0 1 0 3z"/></svg>
        <span>ridgelinepetvisioncare-example.net</span>
      </li>
    </ul>
  </div>
</div>
</body>
</html>
```